Bottle label design for 4 litre jug

Need to create a label for my chemical products please attached label. Must have the side labels, colors must be complimented with logo attached. Come up with a clean yet high end product look to it. the brand name is Varnon Glass cleaner, Trelby Shine Works is the logo,
Redisgn with new updated look, there are a total of 8 labels to be made for oterh products.

Industry/Entity Type

Cleaning industry

Font styles to use
Serif
Other font styles liked:
• Lora Bold, EB garamond, or use any font you choose, clean and bold

Colors
0054AA
0677BA
7BADD7
CADEEF
E8F1F8
0094D4
00A9DD
6FCCEA
C7EBF8
E9F6FB
00AB8E
00BBA5
67D7C9
C6EFE9
E9F9F6

```html
<!DOCTYPE html>
<html lang="en">
<head>
<meta charset="utf-8">
<title>Varnon Glass Cleaner – Jug Label</title>
<link rel="stylesheet" href="https://fonts.googleapis.com/css2?family=Anton&family=Montserrat:ital,wght@0,400;0,500;0,600;0,700;1,400;1,500;1,600;1,700&display=swap">
<style>
  :root{
    --teal-deep:#00a08c;
    --teal:#00ab8e;
    --teal-light:#00bba5;
    --mint:#67d7c9;
    --mint-pale:#c6efe9;
    --panel:#a9e4dc;
    --blue-deep:#0054aa;
    --blue:#0677ba;
    --blue-chip:#0a5fc4;
    --ink:#1d1d1d;
    --logo-box:#2a2a2a;
    --gray-light:#e6e9eb;
    --gray-mid:#cfd5d8;
    --white:#ffffff;
    --page:#d6d6d6;
  }
  *{box-sizing:border-box;margin:0;padding:0}
  html,body{width:1200px;height:960px;overflow:hidden;background:var(--page)}
  body{font-family:"Montserrat",sans-serif;position:relative}
  .label{
    position:absolute;left:30px;top:192px;width:1275px;height:645px;
    transform:scale(0.894);transform-origin:0 0;overflow:hidden;
    background:linear-gradient(172deg,var(--teal-deep) 0%,var(--teal) 45%,#0a9aa4 75%,var(--blue) 100%);
  }
  .label-bg{position:absolute;inset:0}
  .abs{position:absolute}
  .brand-box{left:235px;top:0;width:200px;height:84px;background:var(--logo-box);
    border-radius:0 0 12px 12px;display:flex;align-items:center;justify-content:center;gap:8px;padding:0 14px}
  .brand-dot{width:14px;height:14px;border-radius:50%;background:var(--white);flex:none}
  .brand-name{color:var(--white);font-weight:600;font-size:15px;line-height:1.1;text-transform:uppercase;letter-spacing:.02em}
  .product-name{left:236px;top:112px;font-family:"Anton",sans-serif;font-size:84px;line-height:1;color:var(--blue-deep);letter-spacing:.01em}
  .product-type{left:224px;top:212px;width:414px;height:80px;border:2px solid var(--white);border-radius:12px;
    font-family:"Anton",sans-serif;font-size:66px;line-height:74px;color:var(--mint-pale);padding-left:6px;letter-spacing:.01em;white-space:nowrap}
  .tagline{left:237px;top:306px;color:var(--white);font-weight:500;font-size:17px;line-height:21px}
  .tagline-fr{left:244px;top:356px;color:var(--white);font-style:italic;font-size:15.5px;line-height:19px}
  .divider{left:256px;top:414px;width:70px;height:2px;background:var(--mint)}
  .claim{background:var(--white);color:var(--teal);font-weight:600;font-size:17px;border-radius:6px;padding:3px 9px}
  .claim-fr{color:var(--white);font-style:italic;font-size:15.5px}
  .qms{left:75px;top:540px;display:flex;gap:6px;align-items:flex-start;color:var(--mint);font-weight:600;font-size:14px;line-height:17px}
  .sizes{left:83px;top:590px;display:flex;gap:14px}
  .size{width:42px;height:28px;border-radius:6px;background:var(--blue-chip);color:var(--white);font-size:12px;font-weight:600;display:flex;align-items:center;justify-content:center}
  .sizes .size:last-child{width:44px}
  .cert{background:rgba(255,255,255,.0)}
  .cert-a{left:570px;top:508px;width:92px;height:38px;border-radius:8px;background:rgba(30,30,30,.55)}
  .cert-b{left:582px;top:562px;width:60px;height:50px;border-radius:50%;background:rgba(30,30,30,.55)}
  .directions{left:681px;top:24px;width:278px;height:601px;background:var(--panel);border-radius:16px;padding:26px 12px 0 16px;color:var(--ink);font-size:15.5px;line-height:22px}
  .directions p{margin-bottom:6px}
  .directions .bold{font-weight:700}
  .directions .it{font-style:italic}
  .directions .gap{margin-top:12px}
  .safety{left:972px;top:28px;width:290px;color:var(--white);font-size:10.5px;line-height:12.6px}
  .safety p{margin-bottom:7px}
  .safety b{font-weight:700}
  .safety .fr{font-style:italic}
  .hazard{display:flex;gap:8px;align-items:flex-start;margin:8px 0 10px}
  .hazard svg{flex:none}
  .maker{font-style:italic;font-weight:700;font-size:13.5px;line-height:16px;margin-top:12px}
</style>
</head>
<body>
<main class="label" aria-label="Varnon Glass Cleaner wraparound label">
  <svg class="label-bg" width="1275" height="645" viewBox="0 0 1275 645" aria-hidden="true">
    <defs>
      <linearGradient id="glassFill" x1="0" y1="0" x2="1" y2="1">
        <stop offset="0" stop-color="#eef0f1"/>
        <stop offset="1" stop-color="#d3d8db"/>
      </linearGradient>
    </defs>
    <path d="M40 0 H220 C226 220 248 460 296 645 H40 Z" fill="url(#glassFill)"/>
  </svg>
  <div class="abs" role="img" aria-label="Soft glass texture panel" style="left:40px;top:0;width:180px;height:645px"></div>

  <div class="abs brand-box"><span class="brand-dot"></span><span class="brand-name">Trelby<br>Shine Works</span></div>
  <h1 class="abs product-name">VARNON</h1>
  <div class="abs product-type">GLASS CLEANER</div>

  <p class="abs tagline">Dries fast without leaving a film or streaking.<br>Polishes as it dissolves dirt and dingy film.</p>
  <p class="abs tagline-fr">Sans laisser de pellicules nide trainées. Dissout<br>saleté et pellicule teme et fait briller.</p>
  <div class="abs divider"></div>

  <span class="abs claim" style="left:253px;top:432px">Biodegradeable</span>
  <span class="abs claim-fr" style="left:275px;top:464px">Biodégradeatble</span>
  <span class="abs claim" style="left:278px;top:496px">Non Corrosive</span>
  <span class="abs claim-fr" style="left:297px;top:527px">Non-Corrosif</span>
  <span class="abs claim" style="left:310px;top:557px">Low Carbon Footprint</span>
  <span class="abs claim-fr" style="left:321px;top:588px">Faible Empreinte Ecologiuqe</span>

  <div class="abs qms">
    <svg width="30" height="32" viewBox="0 0 30 32" aria-hidden="true"><rect x="2" y="6" width="22" height="22" rx="4" fill="none" stroke="#67d7c9" stroke-width="2.5"/><path d="M7 16 L13 23 L27 3" fill="none" stroke="#0054aa" stroke-width="3.5" stroke-linecap="round"/></svg>
    <span>Compliant QMS<br>Mfg. Process</span>
  </div>
  <div class="abs sizes"><span class="size">4L</span><span class="size">20L</span><span class="size">205L</span></div>

  <div class="abs cert-a" role="img" aria-label="Eco certification badge"></div>
  <div class="abs cert-b" role="img" aria-label="Environmental partner badge"></div>

  <section class="abs directions">
    <p>Read entire label before using. For industrial and institutional use only.</p>
    <p class="bold">Keep out of reach of children.</p>
    <p class="gap">For windows, glass, mirrors, windshields, ceramic tile, porcelain, etc. Use full strength. Spray on and wipe off with a clean towel or cloth.</p>
    <p class="bold gap">NOT AFFECTED BY FREEZING.</p>
    <p class="it gap">Lire l’étiquette au complet avant d’utiliser le produit. Pour usage industriel ou dans un établissement seulement.</p>
    <p class="it bold">Garder hors de la portée des enfants.</p>
    <p class="it gap">Pour vitres, miroirs, carreaux en céramique, verre, porce-laine, etc. Ne pas diluer. Vaporiser et essuyer à l’aide d’un chiffon propre.</p>
    <p class="it bold gap">NE CRAINT PAS LE GEL.</p>
  </section>

  <section class="abs safety">
    <p><b>WARNING: Causes eye irritation. Prolonged or repeated skin contact may cause irritation.</b></p>
    <p><b>PRECAUTIONS:</b> Wash hands thoroughly after handling. Wear protective gloves/eye protection /face protection. Do not eat, drink or smoke when using this product.</p>
    <p><b>FIRST AID:<br>IF IN EYES:</b> Rinse cautiously with water for several minutes. Remove contact lenses, if present and easy to do. Continue rinsing. If eye irritation persists: get medical attention/advice.</p>
    <p><b>IF SWALLOWED:</b> Rinse mouth. <b>Do NOT</b> induce vomiting. Drink large quantities of water. Call a <b>POISON CENTER</b> or doctor/physician if you feel unwell. If skin irritation occurs: Get medical advice /attention.</p>
    <p><b>See Safety Data Sheet.</b></p>
    <div class="hazard">
      <svg width="70" height="70" viewBox="0 0 70 70" aria-hidden="true"><rect x="14" y="14" width="42" height="42" rx="4" transform="rotate(45 35 35)" fill="none" stroke="#fff" stroke-width="4"/><rect x="32" y="20" width="6" height="20" rx="3" fill="#fff"/><circle cx="35" cy="47" r="3.6" fill="#fff"/></svg>
      <p class="fr" style="margin-top:6px"><b>ATTENTION: Provoque une irritation oculaire. Un contact cutané prolongé ou répété peut provoquer une irritation.</b></p>
    </div>
    <p class="fr"><b>PRÉCAUTIONS:</b> Se laver soigneusement après la manipulation. Porter des gants de protection/protec-tion des yeux/protection du visage. Ne pas manger, boire ou fumer lors de l’utilisation de ce produit.</p>
    <p class="fr"><b>PREMIERS SOINS:</b></p>
    <p class="fr"><b>EN CAS DE CONTACT AVEC LES YEUX:</b> Rincer avec précaution à l’eau pendant plusieurs minutes. En-lever les lentilles de contact si la victime en porte et si elles peuvent être facilement enlevées. Continuer à rincer. Si l’irritation des yeux persiste: consulter un médecin. EN CAS D’INGESTION: Rincer la bouche. NE PAS faire vomir. Boire de grandes quantités d’eau. Appeler le CENTRE ANTIPOISON/un médecin en cas de malaise. En cas d’irritation cutanée: Consulter un médecin.</p>
    <p class="fr">Consulter la fiche de données de sécurité.</p>
    <p class="maker">TRELBY SHINE WORKS<br>Brookmere, Ontario K9X 4P2</p>
  </section>
</main>
</body>
</html>
```